Koala Reach brochure

We need a brochure design for a new company based in Australia called KoalaReach. We are a internet marketing company that adds business to Australian internet directories, Maps, GPS devices and search engines. The system is currently being used in the U.S. and we are bringing it to Australia.
The design should communicate that business owners are going to get more customers coming to their business, more profit and be easily found on the internet and Mobile phones.
At this stage we do not have a logo and are open to the colours that are used.

Target Market(s)

Business owners with Bricks and mortar business. Individuals or large chains or franchises

Industry/Entity Type

Internet

Requirements
Must have
• We have a 100% Guarentee
If your business is not on Page 1 or 2 of Zentrix within 4 months we continue for Free.

Price is $99 per month.
Nice to have
• Bullet points
*Make sure you are seen on maps, directories, Zentrix, and GPS devices.
*Consumers use local search to shop and find businesses today.
*Consumers use Mobile devices to search for your product and service.

```html
<!DOCTYPE html>
<html lang="en">
<head>
<meta charset="utf-8">
<title>Koala Reach Brochure</title>
<link rel="stylesheet" href="https://fonts.googleapis.com/css2?family=Roboto+Condensed:wght@400;700&family=Montserrat:wght@300&family=Arimo:wght@400&family=Tinos:wght@400;700&display=swap">
<style>
  :root {
    --stage: #e8e5e0;
    --green: #3f9a3f;
    --chevron: #4a4a4c;
    --paper-light: #ffffff;
    --paper-mid: #e3e5e8;
    --ink: #111111;
    --blue: #1b6eb3;
    --blue-text: #2a5a8c;
    --yellow: #f7b500;
    --yellow-edge: #e09a00;
    --frame: #222222;
    --logo-disc: #4d6688;
    --white: #ffffff;
  }
  * { margin: 0; padding: 0; box-sizing: border-box; }
  html, body {
    width: 931px; height: 1200px; overflow: hidden;
    background: var(--stage);
  }
  .brochure {
    position: absolute; left: 53px; top: 0;
    width: 824px; height: 1200px; overflow: hidden;
    background: linear-gradient(160deg, var(--paper-light) 0%, var(--paper-mid) 55%, var(--paper-light) 100%);
  }
  .backdrop { position: absolute; inset: 0; }
  .guarantee-headline {
    position: absolute; right: 56px; top: 86px;
    text-align: right;
    font-family: "Roboto Condensed", "Arial Narrow", sans-serif;
    font-weight: 700; font-size: 31px; line-height: 37.5px;
    color: var(--ink);
  }
  .guarantee-headline .free { font-size: 52px; line-height: 60px; }
  .price-tag {
    position: absolute; left: 108px; top: 540px;
    width: 359px; height: 100px;
    background: var(--yellow);
    border-bottom: 4px solid var(--yellow-edge);
    border-radius: 12px;
    transform: rotate(-2.5deg);
    box-shadow: 0 4px 6px rgba(0,0,0,.25);
    display: flex; align-items: center; padding-left: 22px;
    color: var(--ink);
  }
  .price-tag .label {
    font-family: "Arimo", Arial, sans-serif;
    font-size: 37px; line-height: 36px;
  }
  .price-tag .label small { display: block; font-size: 28px; line-height: 32px; }
  .price-tag .amount {
    font-family: "Tinos", "Times New Roman", serif;
    font-weight: 700; font-size: 76px; margin-left: 14px;
    text-shadow: 2px 3px 3px rgba(0,0,0,.35);
  }
  .profit-title {
    position: absolute; right: 56px; top: 700px;
    font-family: "Montserrat", Arial, sans-serif;
    font-weight: 300; font-size: 66px; letter-spacing: 1px;
    color: var(--blue); line-height: 80px;
  }
  .profit-subtitle {
    position: absolute; right: 56px; top: 776px;
    font-family: "Arimo", Arial, sans-serif;
    font-size: 31px; color: var(--ink);
  }
  .company-intro {
    position: absolute; right: 56px; top: 848px;
    text-align: right;
    font-family: "Arimo", Arial, sans-serif;
    font-size: 21px; line-height: 35px; color: var(--blue-text);
  }
  .contact-line {
    position: absolute; right: 56px; top: 1000px;
    font-family: "Arimo", Arial, sans-serif;
    font-size: 30px; color: var(--ink);
  }
  .contact-line .phone { font-size: 41px; }
  .guarantee-banner {
    position: absolute; left: 262px; top: 1075px;
    width: 562px; height: 70px;
  }
  .guarantee-banner .banner-text {
    position: absolute; left: 112px; top: 0; height: 70px;
    display: flex; align-items: center; white-space: nowrap;
    font-family: "Tinos", "Times New Roman", serif;
    font-size: 34px; color: var(--white);
  }
  .guarantee-banner .banner-text strong { font-weight: 400; font-size: 42px; margin: 0 8px; }
  .brand {
    position: absolute; left: 60px; top: 992px; width: 170px;
    display: flex; flex-direction: column; align-items: center;
  }
  .brand .disc {
    width: 130px; height: 130px; border-radius: 50%;
    background: var(--logo-disc);
  }
  .brand .name {
    margin-top: 10px;
    font-family: "Arimo", Arial, sans-serif;
    font-size: 24px; color: var(--ink); white-space: nowrap;
  }
</style>
</head>
<body>
<main class="brochure">
  <svg class="backdrop" viewBox="0 0 824 1200" width="824" height="1200">
    <defs>
      <linearGradient id="photo-tones" x1="0" y1="0" x2="1" y2="1">
        <stop offset="0" stop-color="#d9dde2"/>
        <stop offset="0.5" stop-color="#f2f3f1"/>
        <stop offset="1" stop-color="#c9cdd2"/>
      </linearGradient>
    </defs>
    <polygon class="green-field" points="0,0 824,0 824,660 571,546 0,680" fill="var(--green)"/>
    <polygon class="chevron-band" points="0,680 571,546 824,660 824,686 571,570 0,708" fill="var(--chevron)"/>
    <g class="speech-bubble">
      <polygon points="23,80 558,208 544,473 532,473 563,530 493,473 43,476" fill="var(--frame)" stroke="var(--frame)" stroke-width="16" stroke-linejoin="round"/>
      <polygon points="40,98 542,222 530,460 55,462" fill="url(#photo-tones)" role="img" aria-label="Photo of a businessman looking at a wall of website screenshots"/>
    </g>
    <polygon class="banner-stripe" points="262,1075 300,1075 348,1145 310,1145" fill="var(--ink)"/>
    <polygon class="banner-band" points="308,1075 824,1075 824,1145 356,1145" fill="var(--blue)"/>
  </svg>

  <p class="guarantee-headline">If your<br>business is<br>not on Page 1<br>or 2 of<br>Zentrix<br>within 4<br>months we<br>continue for<br><span class="free">Free</span></p>

  <div class="price-tag">
    <span class="label">price is<small>per month</small></span>
    <span class="amount">$99</span>
  </div>

  <h1 class="profit-title">MORE PROFIT</h1>
  <p class="profit-subtitle">Easily found on the internet and Mobile phones</p>
  <p class="company-intro">We are a internet marketing company that adds<br>business to Australian internet directories, Maps,<br>GPS devices and search engines.</p>
  <p class="contact-line">Contact Us: <span class="phone">055.501.2468</span></p>

  <div class="guarantee-banner">
    <p class="banner-text">We have a <strong>100%</strong> Guarentee</p>
  </div>

  <div class="brand">
    <span class="disc"></span>
    <span class="name">Koala Reach</span>
  </div>
</main>
</body>
</html>
```